Business Card Design Project

We need a Business Card for an Mechanical Engineering firm in Singapore. The design should be Modern & Technical looking, yet eye catching.

Our company deals in Cutting Tools & Machine Accessories for the Manufacturing Industries such as Oil & Gas, Aero Space, etc... For more information on our Company, you can either email me or view our website www.torvalen.com.sg.

We are trying to revamp our image to give our consumers a fresh new perspective to our company, so we welcome all ideas.

Industry/Entity Type

Business

Requirements
Must have
• Must incorporate New Company Logo into the card as shown in Uploaded file.

```html
<!DOCTYPE html>
<html lang="en">
<head>
<meta charset="UTF-8">
<title>Torvalen Tools Business Card</title>
<link rel="stylesheet" href="https://fonts.googleapis.com/css2?family=Arimo:wght@400;700&display=swap">
<style>
  :root {
    --backdrop: #e4e5e7;
    --card: #ffffff;
    --maroon: #9b1b32;
    --maroon-dark: #5e1626;
    --ink: #1e1e1e;
    --label: #3a3a3a;
  }
  * { margin: 0; padding: 0; box-sizing: border-box; }
  html, body {
    width: 1200px;
    height: 900px;
    overflow: hidden;
    background: var(--backdrop);
    font-family: "Arimo", Arial, sans-serif;
  }
  .card {
    position: absolute;
    left: 130px;
    top: 180px;
    width: 946px;
    height: 570px;
    background: var(--card);
  }
  .holder-name {
    position: absolute;
    left: 82px;
    top: 64px;
    font-size: 40px;
    font-weight: 400;
    color: var(--maroon-dark);
  }
  .name-rule {
    position: absolute;
    left: 0;
    top: 114px;
    width: 656px;
    height: 5px;
    background: var(--maroon);
  }
  .holder-title {
    position: absolute;
    left: 110px;
    top: 128px;
    font-size: 26px;
    color: var(--ink);
  }
  .contact-list {
    position: absolute;
    left: 110px;
    top: 214px;
    display: grid;
    grid-template-columns: 96px auto;
    row-gap: 6px;
    font-size: 22px;
    line-height: 26px;
  }
  .contact-label { color: var(--label); }
  .contact-value { color: var(--maroon); }
  .company-block {
    position: absolute;
    right: 604px;
    top: 380px;
    text-align: right;
  }
  .company-name {
    font-size: 29px;
    font-weight: 700;
    color: var(--maroon-dark);
    margin-bottom: 8px;
  }
  .company-address {
    font-style: normal;
    font-size: 23px;
    line-height: 31px;
    color: var(--maroon);
  }
  .brand-mark {
    position: absolute;
    right: 32px;
    top: 388px;
    display: flex;
    align-items: center;
    gap: 18px;
  }
  .brand-dot {
    width: 40px;
    height: 40px;
    border-radius: 50%;
    background: var(--maroon);
  }
  .brand-name {
    font-size: 54px;
    font-weight: 400;
    letter-spacing: 1px;
    color: var(--maroon);
  }
</style>
</head>
<body>
  <section class="card">
    <h1 class="holder-name">Marcus Tan</h1>
    <div class="name-rule"></div>
    <p class="holder-title">President-CEO</p>

    <dl class="contact-list">
      <dt class="contact-label">mobile</dt><dd class="contact-value">65-61234587</dd>
      <dt class="contact-label">email</dt><dd class="contact-value">info@torvalen.com.sg</dd>
      <dt class="contact-label">web</dt><dd class="contact-value">www.torvalen.com.sg</dd>
    </dl>

    <div class="company-block">
      <p class="company-name">Torvalen Tools Pte Ltd</p>
      <address class="company-address">
        27 Kallang Way #03-12<br>
        Kallang Industrial Park<br>
        Singapore 349218
      </address>
    </div>

    <div class="brand-mark">
      <span class="brand-dot"></span>
      <span class="brand-name">TORVALEN TOOLS</span>
    </div>
  </section>
</body>
</html>
```